New Business Card Design Project

I need a design for business cards, i am an electrical business called "Corvane Electrical and Communications" i need the cards to be double sided with the company logo on the back (attached) the front needs to say my company name, web site, email address, telephone number, and ABN number and electrical license number. I am open to different arrangements of the information but would like the background to be incorporating something electrical or something that looks smart. open to all additional ideas also.

The company colours are orange and grey see logo attached.

Business Name: Corvane Electrical and Communications
Website: corvaneelectricalandcomms.example.com.au
Email: brent@corvaneelectricalandcomms.example.com.au
Telephone(mobile): 0481209736
ABN: 71208349162
Lic No: 418273D

Target Market(s)

Business entities, Project Managers, Accounts, Clients

Industry/Entity Type

Electrician

Contact Information for Business Card

I need a design for business cards, i am an electrical business called "Corvane Electrical and Communications" i need the cards to be double sided with the company logo on the back (attached) the front needs to say my company name

Font styles to use
Serif
Sans Serif

Colors
f37122
5c5c5c

Requirements
Must have
• Must have the Logo on the back open to different ways of it being on the back but had in mind to keep it central but again open to other options
Nice to have
• A real modern cool background that is eye catching yet contemporary
Should not have
• No backgrounds of a light bulb or plug or anything like that

```html
<!DOCTYPE html>
<html lang="en">
<head>
<meta charset="utf-8">
<title>Corvane Electrical and Communications – Business Cards</title>
<link rel="stylesheet" href="https://fonts.googleapis.com/css2?family=Questrial&display=swap">
<style>
  :root {
    --stage: #2b2b2b;
    --card: #0b0b0b;
    --orange: #f7a81b;
    --white: #ffffff;
  }
  * { box-sizing: border-box; margin: 0; padding: 0; }
  html, body { width: 1200px; height: 900px; overflow: hidden; }
  body {
    background: var(--stage);
    font-family: "Questrial", "Helvetica Neue", Arial, sans-serif;
    position: relative;
  }
  .card {
    position: absolute;
    width: 620px;
    height: 360px;
    background: var(--card);
    border-radius: 22px;
    overflow: hidden;
    box-shadow: 0 18px 40px rgba(0,0,0,0.55);
  }
  .card--back { left: 90px; top: 70px; }
  .card--front { left: 490px; top: 470px; }

  /* Wordmark lockup */
  .wordmark {
    position: absolute;
    display: flex;
    align-items: center;
    gap: 14px;
  }
  .wordmark__dot {
    width: 22px; height: 22px;
    border-radius: 50%;
    background: var(--orange);
    flex: none;
  }
  .wordmark__name {
    color: var(--white);
    font-size: 30px;
    line-height: 1.1;
    letter-spacing: 1px;
  }
  .card--back .wordmark { left: 110px; top: 120px; }
  .card--back .web {
    position: absolute;
    left: 146px; top: 220px;
    color: var(--white);
    font-size: 15px;
    letter-spacing: 0.3px;
  }

  .card--front .wordmark { right: 40px; top: 50px; }
  .card--front .wordmark__name { font-size: 24px; text-align: right; }

  .licence {
    position: absolute;
    right: 40px; top: 146px;
    color: var(--orange);
    font-size: 14px;
  }
  .licence span { color: var(--white); }
  .rule-licence {
    position: absolute;
    right: 40px; top: 168px;
    width: 250px; height: 1.5px;
    background: var(--orange);
  }

  .person {
    position: absolute;
    left: 30px; top: 174px;
    width: 550px;
  }
  .person__header {
    display: flex;
    align-items: flex-end;
    gap: 12px;
  }
  .person__name {
    color: var(--orange);
    font-size: 26px;
    font-weight: 400;
    line-height: 1.1;
    letter-spacing: 0.5px;
    text-transform: uppercase;
    white-space: nowrap;
  }
  .person__rule {
    flex: 1;
    height: 1.5px;
    background: var(--orange);
    margin-bottom: 6px;
  }
  .person__role {
    color: var(--white);
    font-size: 13px;
    letter-spacing: 1px;
    margin-top: 2px;
  }
  .contacts {
    position: absolute;
    left: 30px; top: 230px;
    list-style: none;
  }
  .contacts li {
    display: flex;
    align-items: center;
    gap: 9px;
    color: var(--white);
    font-size: 14px;
    line-height: 20px;
    white-space: nowrap;
  }
  .contacts svg { width: 12px; height: 12px; flex: none; }

  .footer-bands {
    position: absolute;
    left: 0; bottom: 0;
    width: 620px; height: 130px;
  }
  .abn {
    position: absolute;
    right: 32px; bottom: 72px;
    color: var(--white);
    font-size: 14px;
  }
</style>
</head>
<body>

  <section class="card card--back" aria-label="Business card back">
    <div class="wordmark">
      <span class="wordmark__dot"></span>
      <span class="wordmark__name">Corvane Electrical<br>and Communications</span>
    </div>
    <p class="web">www.corvaneelectricalandcomms.example.com.au</p>
  </section>

  <section class="card card--front" aria-label="Business card front">
    <svg class="footer-bands" viewBox="0 0 620 130" aria-hidden="true">
      <polygon points="0,112 392,72 385,130 0,130" fill="var(--white)"/>
      <polygon points="410,0 620,0 620,130 375,130" fill="var(--orange)"/>
    </svg>

    <div class="wordmark">
      <span class="wordmark__dot"></span>
      <span class="wordmark__name">Corvane Electrical<br>and Communications</span>
    </div>

    <p class="licence">Lic No: <span>418273D</span></p>
    <div class="rule-licence"></div>

    <div class="person">
      <div class="person__header">
        <h1 class="person__name">Brent Marlow</h1>
        <span class="person__rule"></span>
      </div>
      <p class="person__role">DIRECTOR</p>
    </div>

    <ul class="contacts">
      <li>
        <svg viewBox="0 0 24 24" fill="var(--orange)"><path d="M6.6 10.8a15.1 15.1 0 0 0 6.6 6.6l2.2-2.2a1 1 0 0 1 1-.25 11.4 11.4 0 0 0 3.6.57 1 1 0 0 1 1 1V20a1 1 0 0 1-1 1A17 17 0 0 1 3 4a1 1 0 0 1 1-1h3.5a1 1 0 0 1 1 1c0 1.25.2 2.45.57 3.57a1 1 0 0 1-.25 1z"/></svg>
        0481 209-736
      </li>
      <li>
        <svg viewBox="0 0 24 24" fill="none" stroke="var(--orange)" stroke-width="2.4"><rect x="2" y="5" width="20" height="14" rx="1"/><path d="M2 6l10 7 10-7"/></svg>
        brent@corvaneelectricalandcomms.example.com.au
      </li>
      <li>
        <svg viewBox="0 0 24 24" fill="none" stroke="var(--orange)" stroke-width="2.2"><circle cx="12" cy="12" r="10"/><path d="M2 12h20M12 2c3 3 3 17 0 20M12 2c-3 3-3 17 0 20"/></svg>
        www.corvaneelectricalandcomms.example.com.au
      </li>
    </ul>

    <p class="abn">ABN: 71208349162</p>
  </section>

</body>
</html>
```